Namecard for wristwatch company

I run a watch company named Varnik which just launched our first watch. I need a namecard design that is unique and something very different. It should be the same size or smaller than the usual cards. It will be printed on the usual paper as metal/wood are nice but might be too expensive.
I have attached some photos of my watch and the company logo as well.

Target Market(s)
Watch collectors, young professionals
Industry/Entity Type
It Company
Look and feel

```html
<!DOCTYPE html>
<html lang="en">
<head>
<meta charset="utf-8">
<title>Varnik Business Card</title>
<link href="https://fonts.googleapis.com/css2?family=Exo+2:wght@400;500&display=swap" rel="stylesheet">
<style>
  :root {
    --bg: #ececec;
    --card: #ffffff;
    --card-shade: #e9e9e9;
    --blue: #00aeef;
    --ink: #ffffff;
    --ring: #4a4a4a;
    --brand: #3a3a3a;
  }
  * { box-sizing: border-box; margin: 0; padding: 0; }
  html, body { width: 1200px; height: 905px; overflow: hidden; }
  body {
    background: var(--bg);
    font-family: "Exo 2", sans-serif;
    position: relative;
  }
  .card {
    position: absolute;
    width: 510px;
    height: 292px;
    background: radial-gradient(circle at 70% 50%, var(--card) 0%, var(--card-shade) 100%);
    box-shadow: 0 6px 18px rgba(0,0,0,0.12);
    overflow: hidden;
  }
  .card--front { left: 60px; top: 306px; }
  .card--back { left: 630px; top: 306px; }

  .info-panel {
    position: absolute;
    left: 0; top: 0;
    width: 285px; height: 100%;
    background: var(--blue);
    color: var(--ink);
    padding: 30px 24px 0 30px;
  }
  .info-panel__tab {
    position: absolute;
    left: 18px; top: 0;
    width: 14px; height: 34px;
    background: var(--card);
  }
  .person__name {
    font-size: 15px;
    font-weight: 500;
    letter-spacing: 1px;
    text-transform: uppercase;
    margin-left: 16px;
  }
  .person__title {
    font-size: 13px;
    margin-left: 16px;
    margin-bottom: 34px;
  }
  .contact {
    display: grid;
    grid-template-columns: 108px 1fr;
    row-gap: 10px;
    font-size: 10px;
    letter-spacing: 0.5px;
  }
  .contact__item { display: flex; align-items: center; gap: 6px; white-space: nowrap; }
  .contact__item svg { width: 10px; height: 10px; flex: none; }
  .contact__address {
    margin-top: 12px;
    font-size: 11px;
    letter-spacing: 0.4px;
    white-space: nowrap;
  }

  .brand {
    position: absolute;
    display: flex;
    align-items: center;
    gap: 12px;
  }
  .card--front .brand { left: 318px; top: 122px; }
  .card--back .brand { left: 170px; top: 122px; }
  .brand__ring {
    width: 46px; height: 46px;
    border: 5px solid var(--ring);
    border-radius: 50%;
  }
  .brand__name {
    font-size: 26px;
    font-weight: 500;
    color: var(--brand);
    letter-spacing: 1px;
  }
</style>
</head>
<body>
  <section class="card card--front">
    <div class="info-panel">
      <span class="info-panel__tab"></span>
      <p class="person__name">Maren Holst</p>
      <p class="person__title">Managing Director</p>
      <div class="contact">
        <span class="contact__item">
          <svg viewBox="0 0 10 10"><rect x="1" y="3" width="8" height="6" rx="1" fill="#fff"/><rect x="3" y="1" width="4" height="3" fill="#fff"/></svg>
          012 555 0147
        </span>
        <span class="contact__item">
          <svg viewBox="0 0 10 10"><rect x="0.5" y="2" width="9" height="6" fill="#fff"/><path d="M0.5 2 L5 5.5 L9.5 2" stroke="#00aeef" fill="none"/></svg>
          hello@varnik.co
        </span>
        <span class="contact__item">
          <svg viewBox="0 0 10 10"><path d="M2 1 L4 1 L4.5 3.5 L3.3 4.3 Q4.5 6.5 5.7 6.7 L6.5 5.5 L9 6 L9 8 Q5 9.5 1 3 Z" fill="#fff"/></svg>
          012 555 0182
        </span>
        <span class="contact__item">
          <svg viewBox="0 0 10 10"><circle cx="5" cy="5" r="4.2" fill="none" stroke="#fff"/><ellipse cx="5" cy="5" rx="1.8" ry="4.2" fill="none" stroke="#fff"/><line x1="0.8" y1="5" x2="9.2" y2="5" stroke="#fff"/></svg>
          www.varnikstudio.co
        </span>
      </div>
      <p class="contact__address">27 9th Floor, Harbor Line Road KLS</p>
    </div>
    <div class="brand">
      <span class="brand__ring"></span>
      <span class="brand__name">Varnik</span>
    </div>
  </section>

  <section class="card card--back">
    <div class="brand">
      <span class="brand__ring"></span>
      <span class="brand__name">Varnik</span>
    </div>
  </section>
</body>
</html>
```